Pebble Pete''s Funhouse Website Revamp

We have a children's entertainment center that hasn't changed in 20 years and the site looks like it was created 20 years ago. We need a new, modern, clean site that pops. Attached is the new logo that should be used as a style guide.

Current site is: www.pebblepetesfun-example.com

Thanks!
Updates

Designers, thank you all for the amazing work. It was exciting to be able to go through and see all the creativity that came in. I have decided on a design but wanted to share my thanks and appreciation for your time. Warm regards, Morris

Target Market(s)

Mothers with children in the 2 - 14 range.

Industry/Entity Type

Entertainment

```html
<!DOCTYPE html>
<html lang="en">
<head>
<meta charset="utf-8">
<title>Pebble Pete's Funhouse</title>
<link href="https://fonts.googleapis.com/css2?family=Source+Sans+3:wght@400;600;700&display=swap" rel="stylesheet">
<style>
:root{
  --teal:#10b4bb;
  --teal-dark:#0c8f95;
  --green:#7ab342;
  --red:#d7301f;
  --red-dark:#ab2314;
  --orange:#f26a22;
  --orange-dark:#c85313;
  --forest:#1f8b3f;
  --navy:#2f5783;
  --ink:#222;
  --footer:#2b2b2b;
  --white:#fff;
}
*{margin:0;padding:0;box-sizing:border-box}
html,body{width:1200px;height:1064px;overflow:hidden;background:var(--white)}
body{position:relative;font-family:"Source Sans 3",Arial,sans-serif;color:var(--ink)}
.topbar{position:absolute;left:0;top:0;width:1200px;height:58px;background:var(--teal)}
.social{position:absolute;top:20px;left:700px;display:flex;gap:9px}
.social span{width:13px;height:13px;border-radius:2px;display:block}
.social .feed{background:#f39a2a}
.social .net-a{background:#3b5b98}
.social .net-b{background:#5fc4e8}
.search{position:absolute;left:785px;top:13px;width:178px;height:28px;background:var(--white);border-radius:3px;display:flex;align-items:center;padding:0 10px 0 14px;font-size:10px;color:#444}
.search svg{margin-left:auto}
.brand{position:absolute;left:192px;top:88px;width:160px;display:flex;align-items:center;gap:8px}
.brand .dot{width:22px;height:22px;border-radius:50%;background:var(--teal);flex:none}
.brand .name{font-weight:700;font-size:20px;line-height:22px;color:var(--forest)}
.nav{position:absolute;left:407px;top:106px;display:flex;gap:9px}
.nav a{width:92px;height:36px;border-radius:3px;color:var(--white);text-decoration:none;font-weight:700;font-size:14px;display:flex;align-items:center;justify-content:center}
.nav .home{background:var(--green)}
.nav .attr{background:var(--red)}
.nav .part{background:var(--teal)}
.nav .price{background:var(--orange)}
.nav .dir{background:var(--forest)}
.nav .contact{background:var(--navy)}
.slider{position:absolute;left:190px;top:170px;width:814px;height:308px;background:#f4f4f4;box-shadow:0 6px 6px -3px rgba(0,0,0,.18)}
.slide{position:absolute;left:8px;top:10px;width:797px;height:286px;background:linear-gradient(160deg,#8a6b4a 0%,#6a5a4a 40%,#9dcf6e 60%,#3c8fd0 85%,#4b4b4b 100%)}
.dots{position:absolute;right:24px;bottom:18px;display:flex;gap:5px}
.dots i{width:8px;height:8px;border-radius:50%;background:var(--white)}
.dots i.on{background:var(--teal)}
.cards{position:absolute;left:190px;top:518px;display:flex;gap:34px}
.card{width:249px;height:360px;color:var(--white)}
.card .photo{height:111px}
.card .body{padding:17px 15px 0 16px}
.card h2{font-size:20px;font-weight:700;margin-bottom:12px}
.card p{font-size:11.3px;line-height:18.8px;text-align:justify}
.card .more{display:inline-block;margin-top:17px;padding:0 12px;height:28px;line-height:28px;border-radius:3px;font-size:11px;color:var(--white)}
.welcome{background:var(--teal)} .welcome .more{background:var(--teal-dark)}
.welcome .photo{background:linear-gradient(120deg,#d33a2a 0%,#e86aa8 55%,#6f8a5a 100%)}
.attractions{background:var(--orange)} .attractions .more{background:var(--orange-dark)}
.attractions .photo{background:linear-gradient(180deg,#4f7a3c 0%,#8ab360 45%,#cfc6b0 100%)}
.parties{background:var(--red)} .parties .more{background:var(--red-dark)}
.parties .photo{background:linear-gradient(90deg,#a07b50 0%,#e0609a 50%,#3e6fb8 100%)}
.site-links{position:absolute;top:915px;left:0;width:1200px;text-align:center;font-size:12px;font-weight:600}
.site-links span{margin:0 4px}
.address{position:absolute;top:941px;width:1200px;text-align:center;font-size:13.5px;font-weight:600}
.hours{position:absolute;top:969px;width:1200px;text-align:center;font-size:13.5px;font-weight:600}
.legal{position:absolute;left:0;top:1014px;width:1200px;height:50px;background:var(--footer);color:var(--white);font-size:11px;display:flex;align-items:center;justify-content:center}
</style>
</head>
<body>
<header class="topbar">
  <div class="social"><span class="feed"></span><span class="net-a"></span><span class="net-b"></span></div>
  <div class="search">Search Keywords
    <svg width="15" height="15" viewBox="0 0 15 15"><circle cx="6" cy="6" r="4.5" fill="none" stroke="#444" stroke-width="1.8"/><line x1="9.3" y1="9.3" x2="14" y2="14" stroke="#444" stroke-width="2"/></svg>
  </div>
</header>
<div class="brand"><span class="dot"></span><span class="name">Pebble Pete's Funhouse</span></div>
<nav class="nav">
  <a class="home">Home</a><a class="attr">Attractions</a><a class="part">Parties</a><a class="price">Pricing</a><a class="dir">Directions</a><a class="contact">Contact</a>
</nav>
<section class="slider">
  <div class="slide" role="img" aria-label="Kids riding colourful animal-shaped bumper cars indoors"></div>
  <div class="dots"><i class="on"></i><i></i><i></i><i></i></div>
</section>
<section class="cards">
  <article class="card welcome">
    <div class="photo" role="img" aria-label="Two girls climbing on a red playground frame"></div>
    <div class="body"><h2>Welcome</h2>
      <p>Pebble Pete's Funhouse is the Cedar Valley's #1 indoor amusement park for young kids. We cater exclusively to children from infants to around 11 years old. Our climate controlled fun center offers a unique mix of seven different amusement park rides.</p>
      <span class="more">Read More</span></div>
  </article>
  <article class="card attractions">
    <div class="photo" role="img" aria-label="Outdoor splash pad with children playing among trees"></div>
    <div class="body"><h2>Attractions</h2>
      <p>Pebble Pete's Funhouse is the Cedar Valley's #1 indoor amusement park for young kids. We cater exclusively to children from infants to around 11 years old. Our climate controlled fun center offers a unique mix of seven different amusement park rides.</p>
      <span class="more">Read More</span></div>
  </article>
  <article class="card parties">
    <div class="photo" role="img" aria-label="Girl playing on a wooden play structure"></div>
    <div class="body"><h2>Parties</h2>
      <p>Pebble Pete's Funhouse is the Cedar Valley's #1 indoor amusement park for young kids. We cater exclusively to children from infants to around 11 years old. Our climate controlled fun center offers a unique mix of seven different amusement park rides.</p>
      <span class="more">Read More</span></div>
  </article>
</section>
<div class="site-links">Home Page <span>|</span> The Pebble Cafe <span>|</span> Attractions <span>|</span> Parties <span>|</span> Pricing <span>|</span> Group Outings <span>|</span> Directions <span>|</span> Contact Us</div>
<div class="address">215 W. Maple Grove Avenue in Brookfield, Utah Call 801-555-0142.</div>
<div class="hours">Hours: Mon-Thu 11am-9pm, Fri 11am-10pm, Sat 10am-10pm</div>
<footer class="legal">© Copyright 2014 &nbsp;PEBBLE PETES FUNHOUSE . &nbsp;All rights reserved.</footer>
</body>
</html>
```